Home Water Filter Product Labels

We are looking for label design for a home water filter system. Attached files include examples of similar systems with sample labels. The file attached as Lumen Brook logo is our brand/logo and should be incorporated into each label and the text file explains what text should be included on each label of the system. There are a total of 6 labels on the system, 3 of which should be identical except for text and color.
Design Requirements:
-The attached logo should be used on the labels.
-The colors in the label should be used throughout the labels
-Label 1,2,3 should be the same design but different colors like the examples
-Labels Should not be copies of the examples but similar layout with different design
-Design needs to represent a clean feeling but can also be slightly industrial
-The finished files need to have the text editable in case we need to change wording.

Industry/Entity Type

Product

Font styles to use
Sans Serif

Colors

Designer to choose colors to be used in the design.

Requirements
Must have
• ***ALL DESIGN DIMENSIONS ARE IN INCHES**
• Labels 1-3:
• - Same design different colors for each label
• label 6:
• - Must incorporate our logo but include "Crest Line"

```html
<!DOCTYPE html>
<html lang="en">
<head>
<meta charset="utf-8">
<title>Lumen Brook Carbon Filter Label</title>
<link href="https://fonts.googleapis.com/css2?family=Arimo:ital,wght@0,400;0,700;1,400;1,700&display=swap" rel="stylesheet">
<style>
  :root {
    --white: #ffffff;
    --brand-green: #3f8f3a;
    --amber: #f39a00;
    --orange-mid: #ec7a0d;
    --orange-deep: #e6501c;
    --yellow: #fbb900;
    --cream: #fdf19a;
    --label-text: #ffffff;
  }
  * { margin: 0; padding: 0; box-sizing: border-box; }
  html, body { width: 1200px; height: 2182px; overflow: hidden; background: var(--white); }
  .label {
    position: relative; width: 1200px; height: 2182px; overflow: hidden;
    font-family: "Arimo", Arial, sans-serif; color: var(--label-text);
  }
  .label-bg { position: absolute; inset: 0; }
  .brand {
    position: absolute; left: 77px; top: 95px; width: 1047px; height: 186px;
    display: flex; align-items: center; justify-content: center; gap: 32px;
    white-space: nowrap;
  }
  .brand-dot { width: 64px; height: 64px; border-radius: 50%; background: var(--brand-green); flex: none; }
  .brand-name { font-size: 118px; line-height: 1; font-weight: 700; color: var(--brand-green); letter-spacing: 1px; }
  .stage-number {
    position: absolute; left: 852px; top: 772px; width: 348px; height: 200px;
    font-size: 228px; font-weight: 700; font-style: italic; line-height: 200px;
    text-shadow: -8px 4px 0 var(--cream);
  }
  .product-name {
    position: absolute; left: 77px; top: 904px; font-size: 64px; line-height: 1;
    font-weight: 700; color: var(--cream); letter-spacing: 1px; white-space: nowrap;
  }
  .pill {
    position: absolute; left: 0; background: var(--white); color: var(--amber);
    font-weight: 700; font-size: 37px; height: 50px; line-height: 50px;
    padding-left: 77px; border-radius: 0 25px 25px 0; white-space: nowrap;
  }
  .pill-series { top: 1034px; width: 349px; }
  .pill-ops { top: 1289px; width: 565px; }
  .micron { position: absolute; left: 370px; top: 1034px; line-height: 50px; font-size: 37px; font-style: italic; }
  .description {
    position: absolute; left: 77px; top: 1124px; width: 1100px;
    font-size: 37px; line-height: 44px; white-space: nowrap;
  }
  .spec-heading { position: absolute; left: 77px; font-size: 36px; line-height: 1; font-weight: 400; }
  .spec-row { position: absolute; left: 77px; font-size: 36px; line-height: 1; display: flex; white-space: nowrap; }
  .spec-row span:first-child { width: 217px; }
  .spec-row span:nth-child(2) { width: 198px; font-weight: 700; }
  .spec-row span:nth-child(3) { font-weight: 700; }
  .note {
    position: absolute; left: 0; width: 1200px; top: 1759px; text-align: center;
    font-size: 31px; line-height: 38px; white-space: nowrap;
  }
  .warning-rule { position: absolute; left: 0; top: 1914px; width: 1200px; height: 3px; background: var(--white); }
  .warning-tag {
    position: absolute; left: 426px; top: 1889px; width: 349px; height: 54px;
    border: 3px solid var(--white); border-radius: 27px; background: var(--orange-deep);
    text-align: center; line-height: 48px; font-size: 37px; letter-spacing: 1px;
  }
  .warning-text {
    position: absolute; left: 0; width: 1200px; top: 1974px; text-align: center;
    font-size: 37px; line-height: 44px; white-space: nowrap;
  }
</style>
</head>
<body>
<div class="label">
  <svg class="label-bg" width="1200" height="2182" viewBox="0 0 1200 2182" aria-hidden="true">
    <defs>
      <linearGradient id="bodyFill" x1="0" y1="0" x2="0" y2="1">
        <stop offset="0" stop-color="#f39a00"/>
        <stop offset="0.35" stop-color="#ee7d0c"/>
        <stop offset="1" stop-color="#e6501c"/>
      </linearGradient>
      <radialGradient id="glow" cx="0.12" cy="0.3" r="0.4">
        <stop offset="0" stop-color="#e2421b" stop-opacity="0.8"/>
        <stop offset="1" stop-color="#e2421b" stop-opacity="0"/>
      </radialGradient>
      <linearGradient id="numberBar" x1="0" y1="0" x2="1" y2="0">
        <stop offset="0" stop-color="#f08a00"/>
        <stop offset="1" stop-color="#fbb900"/>
      </linearGradient>
    </defs>
    <!-- angled body panel -->
    <polygon points="0,640 1200,470 1200,2182 0,2182" fill="url(#bodyFill)"/>
    <rect x="0" y="560" width="1200" height="900" fill="url(#glow)"/>
    <!-- parallel accent rules -->
    <polygon points="0,700 1200,530 1200,542 0,712" fill="#ffffff"/>
    <polygon points="0,600 620,512 620,518 0,606" fill="#f39a00"/>
    <!-- stage number bar with slanted edge -->
    <polygon points="880,780 1200,780 1200,964 841,964" fill="url(#numberBar)"/>
  </svg>

  <div class="brand">
    <div class="brand-dot"></div>
    <div class="brand-name">LUMEN BROOK</div>
  </div>

  <div class="stage-number">3</div>
  <h1 class="product-name">CARBON FILTER</h1>

  <div class="pill pill-series">Crest Line</div>
  <div class="micron">5 micron</div>

  <p class="description">This filter absorbs the finer suspended organic contaminants<br>such as chlorine, pesticides, herbicides, odors and bad<br>tastes from many different compounds.</p>

  <div class="pill pill-ops">Operating Requirements</div>

  <h2 class="spec-heading" style="top:1385px">TEMPERATURE</h2>
  <div class="spec-row" style="top:1446px"><span>Min</span><span>4°C</span><span>49°F</span></div>
  <div class="spec-row" style="top:1490px"><span>Max</span><span>52°C</span><span>125°F</span></div>

  <h2 class="spec-heading" style="top:1577px">PRESSURE</h2>
  <div class="spec-row" style="top:1641px"><span>Min</span><span>35PSI</span><span>241KPA</span></div>
  <div class="spec-row" style="top:1683px"><span>Max</span><span>80PSI</span><span>551KPA</span></div>

  <p class="note">Manufacturers recommendation is to replace every 6-9 Months<br>depending on incomming water quality.</p>

  <div class="warning-rule"></div>
  <div class="warning-tag">WARNING</div>
  <p class="warning-text">When intended use is for drinking water make sure water is<br>microbiologically safe or adequate disinfection is performed<br>before or after system.</p>
</div>
</body>
</html>
```